Business Card for Multi-Brand Sportswear Company

We are looking for a business card which represents our company and the multiple brands within it.

The company: Fen Athletics (LTD)
The brands: Fen, TavaPuni, ElmStretch, Grit and Rain

Employees using these cards would be representing Fen Athletics, rather than any of the individual brands. You will see a current design within the uploaded files, to give some inspiration. The actual text of the brands is not necessary, but the logos should be on there is some format.

Our creative minds on this are stretched, so we are looking for someone to make this their own, and show us what a good business card should look like.

We may like to get these printed with spot gloss, so keep that in mind with your designs.

www.fenathletics.co.uk

Industry/Entity Type

Business

Contact Information for Business Card

Leo Pemberton-Hale
Operations Manager
(+44) 1632 960 418
Leo@fenathletics.co.uk
www.fenathletics.co.uk

Font styles to use
Sans Serif
Other font styles liked:
• Eurostile

Colors
ffffff

Requirements
Nice to have
• Dark (black) background

```html
<!DOCTYPE html>
<html lang="en">
<head>
<meta charset="utf-8">
<title>Fen Athletics Business Card</title>
<link href="https://fonts.googleapis.com/css2?family=Open+Sans:wght@400;600;700;800&display=swap" rel="stylesheet">
<style>
  :root {
    --backdrop: #1c1c1e;
    --paper: #ffffff;
    --navy: #2e3148;
    --red: #e5232a;
    --ink: #111114;
    --muted: #9a9aa4;
    --lilac: #7c6688;
    --soft-white: #f2f2f5;
  }
  * { box-sizing: border-box; margin: 0; padding: 0; }
  html, body { width: 1200px; height: 1000px; overflow: hidden; }
  body {
    background: var(--backdrop);
    font-family: "Open Sans", Arial, sans-serif;
    position: relative;
  }
  .card {
    position: absolute;
    width: 620px;
    height: 354px;
    border-radius: 26px;
    overflow: hidden;
    background: var(--paper);
    box-shadow: 0 14px 30px rgba(0,0,0,0.45);
  }
  .card--front { left: 290px; top: 96px; }
  .card--back  { left: 290px; top: 540px; }

  /* Front */
  .front-band {
    position: absolute; left: 0; right: 0; bottom: 0; height: 150px;
    background: var(--navy);
  }
  .company-mark {
    position: absolute; left: 0; right: 0; top: 66px;
    display: flex; align-items: center; justify-content: center; gap: 14px;
  }
  .company-mark__dot { width: 16px; height: 16px; background: var(--red); }
  .company-mark__name {
    font-weight: 800; font-size: 46px; color: var(--ink); letter-spacing: 0.5px;
  }
  .brand-row {
    position: absolute; left: 30px; right: 30px; bottom: 0; height: 150px;
    display: flex; align-items: center; justify-content: space-around;
  }
  .brand {
    display: flex; align-items: center; gap: 8px;
    font-weight: 700; font-size: 17px;
  }
  .brand__shape { width: 12px; height: 12px; }
  .brand--grit { color: var(--red); }
  .brand--grit .brand__shape { border-radius: 50%; background: var(--red); }
  .brand--elm { color: var(--muted); }
  .brand--elm .brand__shape { border-radius: 50%; border: 2px solid var(--muted); }
  .brand--fen { color: var(--soft-white); }
  .brand--tava { color: var(--soft-white); }
  .brand--tava .brand__shape { background: var(--lilac); }

  /* Back */
  .back-panel {
    position: absolute; top: 0; bottom: 0; left: 278px; right: 0;
    background: var(--navy);
  }
  .edge-bar {
    position: absolute; width: 14px; background: var(--red); border-radius: 10px;
  }
  .edge-bar--left { left: -4px; top: 60px; height: 250px; }
  .edge-bar--right { right: -4px; top: 36px; height: 210px; }
  .back-mark {
    position: absolute; left: 20px; width: 258px; top: 156px;
    display: flex; align-items: center; justify-content: center; gap: 10px;
  }
  .back-mark__dot { width: 11px; height: 11px; background: var(--red); }
  .back-mark__name { font-weight: 800; font-size: 27px; color: var(--ink); }

  .holder { position: absolute; left: 312px; top: 36px; }
  .holder__name { font-weight: 700; font-size: 24px; color: var(--paper); line-height: 1.15; }
  .holder__name span { color: var(--red); }
  .holder__title { font-weight: 600; font-size: 16px; color: var(--paper); }

  .contact-list {
    position: absolute; left: 312px; top: 126px; list-style: none;
    display: flex; flex-direction: column; gap: 10px;
  }
  .contact {
    display: flex; align-items: center; gap: 14px;
    color: var(--soft-white); font-size: 13.5px; line-height: 1.3;
  }
  .contact__icon {
    width: 40px; height: 40px; flex: none; border-radius: 50%;
    border: 2.5px solid var(--red); background: var(--paper);
    display: flex; align-items: center; justify-content: center;
  }
  .contact__icon svg { width: 20px; height: 20px; }
  .contact .accent { color: var(--red); }
</style>
</head>
<body>

<section class="card card--front" aria-label="Card front">
  <div class="company-mark">
    <span class="company-mark__dot"></span>
    <span class="company-mark__name">Fen Athletics</span>
  </div>
  <div class="front-band"></div>
  <div class="brand-row">
    <div class="brand brand--grit"><span class="brand__shape"></span>Grit and Rain</div>
    <div class="brand brand--elm"><span class="brand__shape"></span>ElmStretch</div>
    <div class="brand brand--fen">Fen</div>
    <div class="brand brand--tava"><span class="brand__shape"></span>TavaPuni</div>
  </div>
</section>

<section class="card card--back" aria-label="Card back">
  <div class="edge-bar edge-bar--left"></div>
  <div class="back-mark">
    <span class="back-mark__dot"></span>
    <span class="back-mark__name">Fen Athletics</span>
  </div>
  <div class="back-panel"></div>
  <div class="edge-bar edge-bar--right"></div>

  <div class="holder">
    <p class="holder__name">Leo <span>Pemberton-Hale</span></p>
    <p class="holder__title">Managing Director</p>
  </div>

  <ul class="contact-list">
    <li class="contact">
      <span class="contact__icon">
        <svg viewBox="0 0 24 24"><path d="M6.6 10.8a15 15 0 0 0 6.6 6.6l2.2-2.2a1 1 0 0 1 1-.25 11.4 11.4 0 0 0 3.6.6 1 1 0 0 1 1 1V20a1 1 0 0 1-1 1A17 17 0 0 1 3 4a1 1 0 0 1 1-1h3.5a1 1 0 0 1 1 1c0 1.25.2 2.45.6 3.6a1 1 0 0 1-.25 1z" fill="#2e3148"/></svg>
      </span>
      <span>+44(0)1632 960418</span>
    </li>
    <li class="contact">
      <span class="contact__icon">
        <svg viewBox="0 0 24 24"><rect x="3" y="6" width="18" height="12" fill="none" stroke="#2e3148" stroke-width="2"/><path d="M3 6l9 7 9-7" fill="none" stroke="#2e3148" stroke-width="2"/></svg>
      </span>
      <span>leo@fenathletics.co.uk</span>
    </li>
    <li class="contact">
      <span class="contact__icon">
        <svg viewBox="0 0 24 24" fill="none" stroke="#2e3148" stroke-width="1.8"><circle cx="12" cy="12" r="9"/><path d="M3 12h18M12 3c3 3 3 15 0 18M12 3c-3 3-3 15 0 18"/></svg>
      </span>
      <span>www.<span class="accent">fenathletics</span>.co.uk</span>
    </li>
    <li class="contact">
      <span class="contact__icon">
        <svg viewBox="0 0 24 24"><path d="M3 12l9-8 9 8h-3v8h-5v-5h-2v5H6v-8z" fill="#2e3148"/></svg>
      </span>
      <span>Kiln Yard, Harrowby,<br>Eastholt, EH42LX</span>
    </li>
  </ul>
</section>

</body>
</html>
```